Bramblewood Card Company Business Cards

We are a trading card store with Glimmorax, sports and other TCG cards, we need a business card design that encompasses a clean cut, modern style with a retro flare. website is bramblewoodcardco.com for reference. Can utilize a comic book era feel or a more modern outdoor feel to utilize the "Pacific Northwest" elements of tress, mountains, etc.

Industry/Entity Type

Trading cards and collectibles

Contact Information for Business Card

business name, email address, phone number, name, owner job title

Font styles to use
Sans Serif

```html
<!DOCTYPE html>
<html lang="en">
<head>
<meta charset="utf-8">
<title>Bramblewood Card Company – Business Cards</title>
<link href="https://fonts.googleapis.com/css2?family=Montserrat:wght@600;700&family=Roboto:wght@400;500&display=swap" rel="stylesheet">
<style>
  :root {
    --sky: #0cbde0;
    --slate: #6c6c6c;
    --paper: #ffffff;
    --stage: #2b2b2d;
    --ink-light: #ffffff;
  }
  * { box-sizing: border-box; margin: 0; padding: 0; }
  html, body { width: 1200px; height: 874px; overflow: hidden; }
  body {
    background: var(--stage);
    font-family: "Roboto", Arial, sans-serif;
    display: flex;
    flex-direction: column;
    align-items: center;
    justify-content: center;
    gap: 32px;
  }
  .card {
    width: 640px;
    height: 366px;
    border-radius: 22px;
    position: relative;
    overflow: hidden;
  }
  .brand-mark {
    display: flex;
    flex-direction: column;
    align-items: center;
    gap: 10px;
    font-family: "Montserrat", Arial, sans-serif;
    font-weight: 700;
    text-align: center;
    text-transform: uppercase;
    letter-spacing: 3px;
    line-height: 1.15;
  }
  .brand-dot { width: 18px; height: 18px; border-radius: 50%; }
  .brand-name { font-size: 30px; }

  /* Front */
  .card-front { background: var(--sky); }
  .card-front .brand-mark {
    position: absolute; left: 0; right: 0; top: 92px; color: var(--ink-light);
  }
  .card-front .brand-dot { background: var(--ink-light); }
  .front-url {
    position: absolute; left: 0; right: 0; bottom: 44px;
    text-align: center; color: var(--ink-light); font-size: 17px;
  }

  /* Back */
  .card-back { background: var(--paper); }
  .card-back .brand-mark {
    position: absolute; left: 0; right: 0; top: 58px; color: var(--slate);
  }
  .card-back .brand-dot { background: var(--sky); }
  .card-back .brand-name { font-size: 26px; }
  .back-band {
    position: absolute; left: 0; right: 0; bottom: 0; height: 170px;
    background: var(--slate);
    border-top: 7px solid var(--sky);
  }
  .person-block {
    position: absolute; left: 0; bottom: 52px;
    display: flex; align-items: center;
  }
  .person {
    width: 250px; text-align: right; padding-right: 18px;
  }
  .person-name {
    font-family: "Montserrat", Arial, sans-serif; font-weight: 600;
    color: var(--sky); font-size: 27px;
  }
  .person-title { color: var(--ink-light); font-size: 17px; margin-top: 2px; }
  .divider { width: 2px; height: 76px; background: var(--ink-light); }
  .contact-list { list-style: none; padding-left: 16px; }
  .contact-list li {
    display: flex; align-items: center; gap: 10px;
    color: var(--ink-light); font-size: 17px; line-height: 1.45;
  }
  .contact-list svg { width: 14px; height: 14px; fill: var(--sky); flex: none; }
</style>
</head>
<body>
  <section class="card card-front">
    <div class="brand-mark">
      <span class="brand-dot"></span>
      <span class="brand-name">Bramblewood<br>Card Company</span>
    </div>
    <p class="front-url">www.bramblewoodcardco.com</p>
  </section>

  <section class="card card-back">
    <div class="brand-mark">
      <span class="brand-dot"></span>
      <span class="brand-name">Bramblewood<br>Card Company</span>
    </div>
    <div class="back-band"></div>
    <div class="person-block">
      <div class="person">
        <p class="person-name">Owen Hale</p>
        <p class="person-title">President</p>
      </div>
      <div class="divider"></div>
      <ul class="contact-list">
        <li>
          <svg viewBox="0 0 24 24" aria-hidden="true"><path d="M6.6 10.8a15 15 0 0 0 6.6 6.6l2.2-2.2a1 1 0 0 1 1-.25 11.4 11.4 0 0 0 3.6.57 1 1 0 0 1 1 1V20a1 1 0 0 1-1 1A17 17 0 0 1 3 4a1 1 0 0 1 1-1h3.5a1 1 0 0 1 1 1c0 1.25.2 2.45.57 3.57a1 1 0 0 1-.25 1z"/></svg>
          555-014-2087
        </li>
        <li>
          <svg viewBox="0 0 24 24" aria-hidden="true"><path d="M2 5h20v14H2z M2 5l10 8 10-8" /></svg>
          info@bramblewoodcardco.com
        </li>
        <li>
          <svg viewBox="0 0 24 24" aria-hidden="true"><circle cx="12" cy="12" r="10"/></svg>
          www.bramblewoodcardco.com
        </li>
      </ul>
    </div>
  </section>
</body>
</html>
```